Business Card for Coastal Tundrabridge Advisory

We need a business card for Coastal Tundrabridge Advisory. The company website address is provided below. The company logo is attached. We provide specialized permafrost services to the mining, transportation, and oil & gas industries. The card should be prepared for:
Matthias Korhonen, PhD.
Coastal Tundrabridge Advisory
PO Box 418259
Quillwater, Alaska 99642
Direct: +1-907-555-0143
Email: mkorhonen@tundrabridgeadvisory.example
Website: www.coastaltundrabridgeadvisory.example

```html
<!DOCTYPE html>
<html lang="en">
<head>
<meta charset="utf-8">
<title>Coastal Tundrabridge Advisory – Business Card</title>
<link href="https://fonts.googleapis.com/css2?family=Montserrat:wght@400;600;700&display=swap" rel="stylesheet">
<style>
  :root {
    --backdrop: #9b9b9b;
    --paper: #ffffff;
    --ink: #111822;
    --ink-soft: #1c232c;
    --night: #131a22;
    --night-deep: #0c1118;
    --frost: #ffffff;
  }
  * { box-sizing: border-box; margin: 0; padding: 0; }
  html, body {
    width: 1093px; height: 1200px; overflow: hidden;
    background: var(--backdrop);
    font-family: "Montserrat", Arial, sans-serif;
    color: var(--ink);
  }
  .card {
    position: absolute; left: 265px;
    width: 580px; height: 364px;
    border-radius: 22px; overflow: hidden;
  }
  .card--front { top: 225px; background: var(--paper); }
  .card--back { top: 616px; background: var(--night); }

  .wordmark {
    position: absolute; left: 30px; top: 186px; width: 200px;
    text-align: center; font-weight: 600; font-size: 12.5px;
    letter-spacing: 0.6px; line-height: 1.3; text-transform: uppercase;
    color: var(--ink);
  }
  .divider {
    position: absolute; left: 241px; top: 122px;
    width: 1.5px; height: 166px; background: var(--ink);
  }
  .identity { position: absolute; left: 251px; top: 120px; }
  .identity__name { font-weight: 700; font-size: 18.5px; line-height: 1.2; }
  .identity__role { font-size: 12.5px; margin-top: 1px; color: var(--ink-soft); }
  .address {
    position: absolute; left: 252px; top: 171px;
    font-size: 13px; line-height: 17px; color: var(--ink-soft);
  }
  .contacts { position: absolute; left: 252px; top: 222px; list-style: none; }
  .contacts li {
    display: flex; align-items: center; height: 25px;
    font-size: 12.3px; color: var(--ink-soft);
  }
  .contacts svg { width: 13px; height: 13px; margin-right: 10px; flex: none; fill: var(--ink); }

  .back-pattern {
    position: absolute; inset: 0;
    background:
      radial-gradient(ellipse at 10% 10%, rgba(255,255,255,0.16), transparent 55%),
      linear-gradient(135deg, var(--night) 0%, var(--night-deep) 100%);
  }
  .back-name {
    position: absolute; left: 0; right: 0; top: 280px;
    text-align: center; font-weight: 600; font-size: 15px;
    letter-spacing: 0.8px; line-height: 1.25; text-transform: uppercase;
    color: var(--frost);
  }
</style>
</head>
<body>
  <section class="card card--front" aria-label="Business card front">
    <div class="wordmark">Coastal Tundrabridge Advisory</div>
    <div class="divider"></div>
    <div class="identity">
      <h1 class="identity__name">Matthias Korhonen, PhD.</h1>
      <p class="identity__role">Managing Director</p>
    </div>
    <p class="address">PO Box 418259<br>Quillwater, Alaska 99642</p>
    <ul class="contacts">
      <li>
        <svg viewBox="0 0 24 24" aria-hidden="true"><path d="M6.6 10.8c1.4 2.8 3.8 5.1 6.6 6.6l2.2-2.2c.3-.3.7-.4 1-.2 1.1.4 2.3.6 3.6.6.6 0 1 .4 1 1V20c0 .6-.4 1-1 1C10.6 21 3 13.4 3 4c0-.6.4-1 1-1h3.5c.6 0 1 .4 1 1 0 1.3.2 2.5.6 3.6.1.3 0 .7-.2 1z"/></svg>
        +1-907-555-0143
      </li>
      <li>
        <svg viewBox="0 0 24 24" aria-hidden="true"><path d="M2 5h20v14H2z M2 5l10 7 10-7" /><path d="M2 6.5l10 7 10-7V19H2z" fill="#fff" opacity="0"/></svg>
        mkorhonen@tundrabridgeadvisory.example
      </li>
      <li>
        <svg viewBox="0 0 24 24" aria-hidden="true"><path d="M12 2a10 10 0 1 0 0 20 10 10 0 0 0 0-20zm-1 17.9A8 8 0 0 1 4.2 10.2L9 15v1a2 2 0 0 0 2 2zm6.9-2.5A2 2 0 0 0 16 16h-1v-3a1 1 0 0 0-1-1H8v-2h2a1 1 0 0 0 1-1V7h2a2 2 0 0 0 2-2v-.4a8 8 0 0 1 2.9 12.8z"/></svg>
        www.coastaltundrabridgeadvisory.example
      </li>
    </ul>
  </section>

  <section class="card card--back" aria-label="Business card back">
    <div class="back-pattern" role="img" aria-label="Tonal repeating company name pattern on dark background"></div>
    <div class="back-name">Coastal Tundrabridge<br>Advisory</div>
  </section>
</body>
</html>
```